Oral Surgeon Referral Pads

Hello. We need referral pads for Dr Elsabet Quorvane, DDS board certified oral surgeon's new office - Harrowgate Dunmere Oral & Maxillofacial Surgery. See logo uploaded. See some images we would like included
Updates

Designs look the same

Font styles to use
Serif
Script

Colors
00AB8E
00BBA5
67D7C9
C6EFE9
E9F9F6

Requirements
Must have
• Color Pantone 623c. Also foldable business cards

```html
<!DOCTYPE html>
<html lang="en">
<head>
<meta charset="utf-8">
<title>Harrowgate Dunmere Oral &amp; Maxillofacial Surgery – Referral Pads and Cards</title>
<link rel="stylesheet" href="https://fonts.googleapis.com/css2?family=Lora:wght@500;600&family=Open+Sans:wght@400;600;700&display=swap">
<style>
  :root {
    --teal-deep: #00806b;
    --teal: #00AB8E;
    --teal-bright: #00BBA5;
    --teal-soft: #67D7C9;
    --teal-pale: #C6EFE9;
    --teal-mist: #E9F9F6;
    --ink: #2a2a2a;
    --paper: #ffffff;
    --backdrop: #636363;
  }
  * { margin: 0; padding: 0; box-sizing: border-box; }
  html, body { width: 1200px; height: 692px; overflow: hidden; background: var(--backdrop); }
  body { position: relative; font-family: "Open Sans", Arial, sans-serif; color: var(--ink); }

  .sheet { position: absolute; background: var(--paper); }
  .pad-referral { left: 66px; top: 118px; width: 324px; height: 454px; }
  .pad-procedure { left: 437px; top: 119px; width: 324px; height: 453px; }
  .card { position: absolute; left: 826px; width: 284px; height: 162px; border-radius: 14px; overflow: hidden; }
  .card-front { top: 149px; background: var(--paper); }
  .card-back { top: 368px; background: var(--teal); }

  .t { position: absolute; line-height: 1; white-space: nowrap; font-size: 7.2px; }
  .accent { color: var(--teal-deep); }
  .serif { font-family: "Lora", Georgia, serif; }
  .bold { font-weight: 600; }
  .semi { font-weight: 600; }
  .rule { position: absolute; height: 1px; background: var(--teal); }
  .vrule { position: absolute; width: 1px; background: var(--teal); }
  .box { display: inline-block; width: 4px; height: 4px; border: 0.8px solid var(--teal-deep); margin-right: 3px; vertical-align: 0; }
  .abs-box { position: absolute; width: 4px; height: 4px; border: 0.8px solid var(--teal-deep); }

  .brand { position: absolute; text-align: center; color: var(--teal-deep); font-family: "Lora", Georgia, serif; font-weight: 500; line-height: 1.25; }
  .brand-name { display: block; font-size: 1.55em; line-height: 1.15; }
  .brand-mark { display: block; margin: 0 auto 4px; border-radius: 50%; border: 1.2px solid currentColor; }

  .contact-row { display: flex; align-items: center; gap: 2px; }
  .contact-row svg { width: 6px; height: 6px; flex: none; }

  .bottom-band { position: absolute; left: 0; right: 0; bottom: 0; height: 8px; background: var(--teal); }
  .notes-frame { position: absolute; left: 27px; top: 260px; width: 268px; height: 179px; border: 1.5px solid var(--teal); background: var(--teal-mist); }
  .card-tab { position: absolute; right: 0; top: 71px; width: 6px; height: 20px; background: var(--teal); }
</style>
</head>
<body>

<section class="sheet pad-referral">
  <div class="t accent serif bold" style="left:23px;top:33px;font-size:9.5px;">Dr Elsabet Quorvane</div>

  <div class="t" style="left:23px;top:62px;font-size:7px;line-height:10.3px;">
    <div class="contact-row"><svg viewBox="0 0 10 10"><path d="M5 0.5a3.4 3.4 0 0 0-3.4 3.4C1.6 6.4 5 9.5 5 9.5s3.4-3.1 3.4-5.6A3.4 3.4 0 0 0 5 0.5z" fill="var(--teal-deep)"/><circle cx="5" cy="3.9" r="1.2" fill="#fff"/></svg>Your address, City State, Zip 1234</div>
    <div class="contact-row"><svg viewBox="0 0 10 10"><path d="M2 1l2 0 1 2.5-1.3 1a6 6 0 0 0 2.8 2.8l1-1.3L10 7v2c0 .6-.4 1-1 1C4.5 10 0 5.5 0 1c0-.6.4-1 1-1z" fill="var(--teal-deep)"/></svg>123 456 789</div>
    <div class="contact-row"><svg viewBox="0 0 10 10"><rect x="1" y="3" width="8" height="6" fill="var(--teal-deep)"/><rect x="3" y="0.5" width="4" height="3" fill="none" stroke="var(--teal-deep)"/></svg>123 456 789</div>
    <div class="contact-row"><svg viewBox="0 0 10 10"><rect x="0.5" y="2" width="9" height="6.5" fill="none" stroke="var(--teal-deep)"/><path d="M0.5 2l4.5 4 4.5-4" fill="none" stroke="var(--teal-deep)"/></svg>info@harrowgatedunmere.com</div>
    <div class="contact-row"><svg viewBox="0 0 10 10"><circle cx="5" cy="5" r="4.3" fill="none" stroke="var(--teal-deep)"/><path d="M0.7 5h8.6M5 0.7c-2.4 2.4-2.4 6.2 0 8.6M5 0.7c2.4 2.4 2.4 6.2 0 8.6" fill="none" stroke="var(--teal-deep)" stroke-width="0.7"/></svg>www.yourwebsite.com</div>
  </div>

  <div class="brand" style="left:150px;top:26px;width:158px;font-size:9.5px;">
    <span class="brand-mark" style="width:22px;height:22px;"></span>
    <span class="brand-name">Harrowgate Dunmere</span>
    Oral &amp; Maxillofacial Surgery
  </div>

  <div class="t" style="left:23px;top:121px;">Today’ s Date &nbsp; DD &nbsp;&nbsp;&nbsp; / &nbsp;&nbsp;&nbsp; MM &nbsp;&nbsp;&nbsp; / &nbsp;&nbsp;&nbsp; YYY</div>
  <div class="rule" style="left:23px;top:133px;width:278px;"></div>

  <div class="t" style="left:24px;top:140px;">Apt.date</div>
  <div class="t" style="left:76px;top:140px;">DD &nbsp;&nbsp;&nbsp; / &nbsp;&nbsp; / MM &nbsp;&nbsp; / &nbsp;&nbsp; YYYY</div>
  <div class="t" style="left:199px;top:140px;">Day</div>
  <div class="rule" style="left:23px;top:154px;width:187px;"></div>

  <div class="t" style="left:218px;top:140px;"><span class="box"></span>Mon</div>
  <div class="t" style="left:252px;top:140px;"><span class="box"></span>Tues</div>
  <div class="t" style="left:218px;top:150px;"><span class="box"></span>Wed</div>
  <div class="t" style="left:252px;top:150px;"><span class="box"></span>Thurs</div>
  <div class="t" style="left:218px;top:160px;"><span class="box"></span>Fri</div>
  <div class="t" style="left:252px;top:160px;"><span class="box"></span>Sat</div>
  <div class="t" style="left:218px;top:170px;"><span class="box"></span>Sun</div>

  <div class="t" style="left:23px;top:159px;">Time</div>
  <div class="t" style="left:140px;top:159px;">AM/PM</div>
  <div class="rule" style="left:23px;top:172px;width:187px;"></div>

  <div class="t" style="left:23px;top:176px;">Patient’ s Name</div>
  <div class="rule" style="left:23px;top:188px;width:278px;"></div>
  <div class="t" style="left:23px;top:195px;">Patient’ Phone Number</div>
  <div class="rule" style="left:23px;top:208px;width:278px;"></div>
  <div class="t" style="left:23px;top:213px;">Referred by</div>
  <div class="rule" style="left:23px;top:225px;width:278px;"></div>
  <div class="t" style="left:24px;top:232px;">Additional Comments</div>

  <div class="t" style="left:23px;top:267px;font-size:6.8px;line-height:10px;">You can save time by going online.Register and update your health today<br>at www.yourwebsite.com</div>

  <div class="t" style="left:21px;top:336px;width:280px;display:flex;justify-content:space-between;font-size:6.8px;">
    <span>1</span><span>2</span><span>3</span><span>4</span><span>5</span><span>6</span><span>7</span><span>8</span><span>9</span><span>10</span><span>11</span><span>12</span><span>13</span><span>14</span><span>15</span><span>16</span>
  </div>
  <div class="t" style="left:70px;top:350px;width:234px;font-size:6.8px;">
    <span style="position:absolute;left:2px;">A</span><span style="position:absolute;left:19px;">B</span><span style="position:absolute;left:33px;">C</span><span style="position:absolute;left:50px;">D</span><span style="position:absolute;left:67px;">E</span><span style="position:absolute;left:84px;">F</span><span style="position:absolute;left:103px;">G</span><span style="position:absolute;left:124px;">H</span><span style="position:absolute;left:142px;">I</span><span style="position:absolute;left:160px;">J</span>
  </div>
  <div class="rule" style="left:21px;top:361px;width:282px;"></div>
  <div class="vrule" style="left:162px;top:336px;height:52px;"></div>
  <div class="t" style="left:70px;top:370px;width:234px;font-size:6.8px;">
    <span style="position:absolute;left:0px;">T</span><span style="position:absolute;left:16px;">S</span><span style="position:absolute;left:31px;">R</span><span style="position:absolute;left:48px;">Q</span><span style="position:absolute;left:66px;">P</span><span style="position:absolute;left:82px;">O</span><span style="position:absolute;left:103px;">N</span><span style="position:absolute;left:121px;">M</span><span style="position:absolute;left:141px;">L</span><span style="position:absolute;left:162px;">K</span><span style="position:absolute;left:181px;">14</span><span style="position:absolute;left:201px;">15</span><span style="position:absolute;left:218px;">16</span>
  </div>
  <div class="t" style="left:22px;top:382px;width:284px;display:flex;justify-content:space-between;font-size:6.8px;">
    <span>32</span><span>31</span><span>30</span><span>29</span><span>28</span><span>27</span><span>26</span><span>25</span><span>24</span><span>23</span><span>22</span><span>21</span><span>20</span><span>19</span><span>18</span><span>17</span>
  </div>

  <div class="bottom-band"></div>
</section>

<section class="sheet pad-procedure">
  <div class="t" style="left:44px;top:47px;font-size:6px;">PROCEDURE</div>
  <div class="t" style="left:45px;top:59px;font-size:6px;"><span class="box"></span>Extraction</div>
  <div class="t" style="left:95px;top:58px;font-size:6px;"><span class="box"></span>Implants</div>
  <div class="t" style="left:146px;top:59px;font-size:6px;"><span class="box"></span>Consultation</div>
  <div class="t" style="left:202px;top:58px;font-size:6px;"><span class="box"></span>Radiogrphs</div>

  <div class="t semi" style="left:21px;top:79px;font-size:7.5px;line-height:10.6px;">
    <div><span class="box"></span>Wisdom Teeth</div>
    <div><span class="box"></span>Extraction</div>
    <div><span class="box"></span>Implants</div>
    <div><span class="box"></span>Bone Grafing</div>
    <div><span class="box"></span>Exposure and bonding</div>
    <div><span class="box"></span>Biopsy(SOFT or Hard Tissue)</div>
  </div>

  <div class="abs-box" style="left:145px;top:81px;"></div>
  <div class="abs-box" style="left:145px;top:92px;"></div>
  <div class="abs-box" style="left:145px;top:102px;"></div>
  <div class="abs-box" style="left:145px;top:113px;"></div>
  <div class="abs-box" style="left:145px;top:123px;"></div>
  <div class="abs-box" style="left:145px;top:134px;"></div>
  <div class="abs-box" style="left:145px;top:144px;"></div>
  <div class="rule" style="left:153px;top:156px;width:41px;"></div>
  <div class="rule" style="left:153px;top:166px;width:41px;"></div>

  <div class="t semi" style="left:217px;top:89px;font-size:7.5px;line-height:10.6px;">
    <div><span class="box"></span>Veltrix</div>
    <div><span class="box"></span>Orendale</div>
    <div><span class="box"></span>Calyra</div>
    <div><span class="box"></span>Torvin</div>
    <div><span class="box"></span>Other</div>
  </div>
  <div class="rule" style="left:224px;top:146px;width:41px;"></div>
  <div class="rule" style="left:224px;top:156px;width:41px;"></div>

  <div class="t" style="left:44px;top:171px;font-size:7.5px;">Surgical Template</div>
  <div class="t semi" style="left:21px;top:183px;font-size:7.5px;"><span class="box"></span>To be provided by Restorative dentist</div>
  <div class="t semi" style="left:179px;top:183px;font-size:7.5px;"><span class="box"></span>To be fabricated by the surgeon</div>
  <div class="t semi" style="left:21px;top:194px;font-size:7.5px;"><span class="box"></span>Other</div>
  <div class="rule" style="left:63px;top:200px;width:101px;"></div>

  <div class="t" style="left:44px;top:211px;font-size:7.5px;">Radfographs</div>
  <div class="t semi" style="left:21px;top:222px;font-size:7.5px;"><span class="box"></span>Being Mafled/emafled</div>
  <div class="t semi" style="left:117px;top:222px;font-size:7.5px;"><span class="box"></span>Given to the Patient</div>
  <div class="t semi" style="left:212px;top:222px;font-size:7.5px;"><span class="box"></span>Please Take</div>
  <div class="t semi" style="left:21px;top:233px;font-size:7.5px;"><span class="box"></span>Other</div>
  <div class="rule" style="left:63px;top:238px;width:101px;"></div>

  <div class="notes-frame"></div>
</section>

<section class="card card-front">
  <div class="brand" style="left:6px;top:10px;width:116px;font-size:6.6px;">
    <span class="brand-mark" style="width:16px;height:16px;margin-bottom:3px;"></span>
    <span class="brand-name">Harrowgate Dunmere</span>
    Oral &amp; Maxillofacial Surgery
  </div>
  <div class="t accent serif bold" style="right:12px;top:70px;font-size:11px;">Dr Elsabet Quorvane,</div>
  <div class="t" style="right:12px;top:84px;font-size:7.5px;">DDS board certified</div>
  <div class="card-tab"></div>

  <div class="t" style="left:11px;top:88px;font-size:8px;line-height:10px;">Your address, City<br>State, Zip 1234</div>
  <div class="t" style="left:11px;top:123px;font-size:8px;line-height:10.2px;">
    <div class="contact-row"><svg viewBox="0 0 10 10"><path d="M2 1l2 0 1 2.5-1.3 1a6 6 0 0 0 2.8 2.8l1-1.3L10 7v2c0 .6-.4 1-1 1C4.5 10 0 5.5 0 1c0-.6.4-1 1-1z" fill="var(--teal-deep)"/></svg>123 456 789</div>
    <div class="contact-row"><svg viewBox="0 0 10 10"><rect x="0.5" y="2" width="9" height="6.5" fill="none" stroke="var(--teal-deep)"/><path d="M0.5 2l4.5 4 4.5-4" fill="none" stroke="var(--teal-deep)"/></svg>info@harrowgatedunmere.com</div>
    <div class="contact-row"><svg viewBox="0 0 10 10"><circle cx="5" cy="5" r="4.3" fill="none" stroke="var(--teal-deep)"/><path d="M0.7 5h8.6M5 0.7c-2.4 2.4-2.4 6.2 0 8.6M5 0.7c2.4 2.4 2.4 6.2 0 8.6" fill="none" stroke="var(--teal-deep)" stroke-width="0.7"/></svg>www.hdoms-care.com</div>
  </div>
</section>

<section class="card card-back">
  <div class="brand" style="left:0;top:24px;width:284px;font-size:12px;color:#ffffff;">
    <span class="brand-mark" style="width:40px;height:40px;margin-bottom:10px;"></span>
    <span class="brand-name">Harrowgate Dunmere</span>
    Oral &amp; Maxillofacial Surgery
  </div>
</section>

</body>
</html>
```